Modern Business Card

Modern professional business card with more than just logo and demographic info. Something memorable.

We are a trendy/modern chiropractic group with an emphasis on neurology, hence the minimalist-type brain logo. We want to convey that modern and technical aspect with professionalism and the elite nature of our practice environment.

```html
<!DOCTYPE html>
<html lang="en">
<head>
<meta charset="utf-8">
<title>Vantage Chiropractic – Business Card</title>
<link rel="stylesheet" href="https://fonts.googleapis.com/css2?family=Quattrocento:wght@400&family=Saira+Semi+Condensed:wght@600&family=Roboto:wght@400&display=swap">
<style>
  :root {
    --stage: #b9b9b9;
    --card: #f1f1f1;
    --ink: #1d1a1b;
    --brand-blue: #3d62a0;
    --brand-brown: #3f3436;
    --text: #3a3a3a;
  }
  * { margin: 0; padding: 0; box-sizing: border-box; }
  html, body {
    width: 1200px; height: 576px; overflow: hidden;
    background: var(--stage);
  }
  .stage { position: relative; width: 1200px; height: 576px; }
  .card {
    position: absolute;
    top: 138px;
    width: 484px; height: 294px;
    background: var(--card);
    border-radius: 8px;
    overflow: hidden;
    box-shadow: 0 3px 6px rgba(0,0,0,0.25);
  }
  .card--front { left: 82px; }
  .card--back { left: 602px; width: 481px; height: 292px; }

  .wordmark {
    font-family: "Quattrocento", Georgia, serif;
    font-weight: 400;
    color: var(--ink);
    line-height: 0.95;
  }
  .wordmark__main { display: block; letter-spacing: 0.5px; }
  .wordmark__sub { display: block; letter-spacing: 1px; }

  /* Front */
  .front-brand {
    position: absolute; left: 78px; top: 94px;
    display: flex; align-items: center; gap: 14px;
  }
  .brand-square { width: 22px; height: 22px; background: var(--brand-blue); }
  .front-brand .wordmark__main { font-size: 56px; }
  .front-brand .wordmark__sub { font-size: 29px; }
  .front-web {
    position: absolute; left: 0; right: 0; top: 247px;
    display: flex; justify-content: center; align-items: center; gap: 18px;
    font-family: "Roboto", Arial, sans-serif; font-size: 12.5px; color: #222;
  }
  .front-web svg { display: block; }
  .front-band {
    position: absolute; left: 0; bottom: 0; width: 100%; height: 13px;
    display: flex;
  }
  .front-band__blue { flex: 1; background: var(--brand-blue); }
  .front-band__brown { flex: 1; background: var(--brand-brown); }

  /* Back */
  .back-brand { position: absolute; left: 30px; top: 30px; }
  .back-brand .wordmark__main { font-size: 38px; }
  .back-brand .wordmark__sub { font-size: 21px; }
  .person { position: absolute; left: 29px; top: 113px; }
  .person__name {
    font-family: "Saira Semi Condensed", "Arial Narrow", sans-serif;
    font-weight: 600; font-size: 19px; color: var(--brand-blue);
  }
  .person__title {
    font-family: "Quattrocento", Georgia, serif;
    font-size: 12px; color: var(--text); margin-top: 1px;
  }
  .contact {
    position: absolute; left: 29px; top: 176px;
    list-style: none;
    font-family: "Quattrocento", Georgia, serif; font-size: 12px; color: var(--text);
  }
  .contact li { display: flex; align-items: center; gap: 10px; height: 18px; }
  .contact svg { width: 11px; height: 11px; fill: var(--brand-blue); flex: none; }
  .address {
    position: absolute; left: 29px; top: 234px;
    font-family: "Quattrocento", Georgia, serif; font-size: 12px;
    color: var(--text); line-height: 18px; font-style: normal;
  }
</style>
</head>
<body>
<main class="stage">

  <section class="card card--front" aria-label="Card front">
    <div class="front-brand">
      <span class="brand-square"></span>
      <div class="wordmark">
        <span class="wordmark__main">VANTAGE</span>
        <span class="wordmark__sub">CHIROPRACTIC</span>
      </div>
    </div>
    <div class="front-web">
      <svg width="34" height="4" viewBox="0 0 34 4"><polygon points="0,2 34,0.5 34,3.5" fill="var(--brand-blue)"/></svg>
      <span>www.vantagechiropractic.com</span>
      <svg width="34" height="4" viewBox="0 0 34 4"><polygon points="0,0.5 34,2 0,3.5" fill="var(--brand-blue)"/></svg>
    </div>
    <div class="front-band">
      <span class="front-band__blue"></span>
      <span class="front-band__brown"></span>
    </div>
  </section>

  <section class="card card--back" aria-label="Card back">
    <div class="back-brand wordmark">
      <span class="wordmark__main">VANTAGE</span>
      <span class="wordmark__sub">CHIROPRACTIC</span>
    </div>
    <div class="person">
      <p class="person__name">Alex Morgan Reed</p>
      <p class="person__title">Managing Director</p>
    </div>
    <ul class="contact">
      <li>
        <svg viewBox="0 0 12 12"><path d="M1 3.5C1 2 2.5 1.5 6 1.5S11 2 11 3.5V5H8.5V4H3.5V5H1Z M2.5 6.5h7L11 10.5H1Z"/></svg>
        555-010-2040
      </li>
      <li>
        <svg viewBox="0 0 12 12"><path d="M0.5 2.5h11v7h-11Z M1.5 3.3 6 6.8 10.5 3.3v-0.1h-9Z" fill-rule="evenodd"/></svg>
        alex@vantagechiropractic.com
      </li>
      <li>
        <svg viewBox="0 0 12 12"><path d="M6 0.8a5.2 5.2 0 1 0 0.01 0Z M6 1.8c-0.8 0.9-1.3 2.4-1.3 4.2s0.5 3.3 1.3 4.2c0.8-0.9 1.3-2.4 1.3-4.2S6.8 2.7 6 1.8Z M1.9 5.5h8.2v1H1.9Z" fill-rule="evenodd"/></svg>
        www.vantagechiropractic.com
      </li>
    </ul>
    <address class="address">
      48 Example Ave., Sample City,<br>
      Sample Town, US 000000
    </address>
  </section>

</main>
</body>
</html>
```